CFO services graphic design

I own a business consulting firm called Thornfield Advisory and we need a graphic for CFO services in our colours and branding. The attached file "CFO services to be put into Thornfield advisory theme", shows the content for the design. The two other files show the theme and colours for the new design.

```html
<!DOCTYPE html>
<html lang="en">
<head>
<meta charset="utf-8">
<title>Thornfield Advisory – CFO Services</title>
<link rel="stylesheet" href="https://fonts.googleapis.com/css2?family=Open+Sans:wght@400;600;700;800&display=swap">
<style>
  :root {
    --brand-navy: #1f3a5f;
    --brand-navy-frame: #e3e9f1;
    --brand-gold: #c9a227;
    --brand-gold-frame: #f7f0da;
    --ink-dark: #16283f;
    --ink-light: #ffffff;
    --page: #ffffff;
  }
  html, body {
    margin: 0;
    padding: 0;
    overflow: hidden;
    background: var(--page);
  }
  .canvas {
    position: relative;
    width: 1200px;
    height: 1000px;
    background: var(--page);
    font-family: "Open Sans", Arial, sans-serif;
    overflow: hidden;
  }
  .connectors {
    position: absolute;
    inset: 0;
  }
  .hub-label {
    position: absolute;
    left: 480px;
    top: 380px;
    width: 240px;
    height: 240px;
    display: flex;
    align-items: center;
    justify-content: center;
    text-align: center;
    color: var(--ink-light);
    font-weight: 700;
    font-size: 24px;
    line-height: 29px;
    letter-spacing: 0.4px;
  }
  .service {
    position: absolute;
    width: 212px;
    height: 131px;
    box-sizing: border-box;
    border: 3px solid;
    border-radius: 20px;
    padding: 8px;
  }
  .service__inner {
    width: 100%;
    height: 100%;
    box-sizing: border-box;
    border-radius: 11px;
    display: flex;
    flex-direction: column;
    align-items: center;
    justify-content: center;
    text-align: center;
    font-size: 14px;
    line-height: 18px;
    font-weight: 700;
    padding: 0 6px;
  }
  .service__detail { font-weight: 400; }
  .service--navy { border-color: var(--brand-navy); background: var(--brand-navy-frame); }
  .service--navy .service__inner { background: var(--brand-navy); color: var(--ink-light); }
  .service--gold { border-color: var(--brand-gold); background: var(--brand-gold-frame); }
  .service--gold .service__inner { background: var(--brand-gold); color: var(--ink-dark); }
  .service--cost { left: 494px; top: 91px; height: 130px; }
  .service--capital { left: 797px; top: 196px; }
  .service--investment { left: 879px; top: 434px; }
  .service--performance { left: 797px; top: 672px; }
  .service--budgeting { left: 494px; top: 778px; }
  .service--risk { left: 191px; top: 672px; }
  .service--compliance { left: 109px; top: 434px; }
  .service--communication { left: 191px; top: 196px; }
</style>
</head>
<body>
<main class="canvas">
  <svg class="connectors" width="1200" height="1000" viewBox="0 0 1200 1000" aria-hidden="true">
    <g stroke-width="3">
      <line x1="600" y1="220" x2="600" y2="363" stroke="var(--brand-navy)"/>
      <line x1="600" y1="635" x2="600" y2="778" stroke="var(--brand-navy)"/>
      <line x1="321" y1="500" x2="464" y2="500" stroke="var(--brand-navy)"/>
      <line x1="736" y1="500" x2="879" y2="500" stroke="var(--brand-navy)"/>
      <line x1="696" y1="404" x2="799" y2="301" stroke="var(--brand-gold)"/>
      <line x1="696" y1="596" x2="799" y2="699" stroke="var(--brand-gold)"/>
      <line x1="504" y1="596" x2="401" y2="699" stroke="var(--brand-gold)"/>
      <line x1="504" y1="404" x2="401" y2="301" stroke="var(--brand-gold)"/>
    </g>
    <circle cx="600" cy="500" r="136" fill="var(--brand-gold-frame)" stroke="var(--brand-gold)" stroke-width="3"/>
    <circle cx="600" cy="500" r="120" fill="var(--brand-navy)"/>
    <g fill="var(--brand-navy)">
      <circle cx="600" cy="363" r="7"/>
      <circle cx="600" cy="635" r="7"/>
      <circle cx="464" cy="500" r="7"/>
      <circle cx="736" cy="500" r="7"/>
    </g>
    <g fill="var(--brand-gold)">
      <circle cx="696" cy="404" r="7"/>
      <circle cx="696" cy="596" r="7"/>
      <circle cx="504" cy="596" r="7"/>
      <circle cx="504" cy="404" r="7"/>
    </g>
  </svg>

  <div class="hub-label">CHIEF FINANCIAL<br>OFFICER</div>

  <div class="service service--navy service--cost">
    <div class="service__inner">Cost Accounting &amp;<br>Cost Management</div>
  </div>
  <div class="service service--gold service--capital">
    <div class="service__inner">Capital Structure &amp;<br>The Cost of Capital</div>
  </div>
  <div class="service service--navy service--investment">
    <div class="service__inner">Long-term &amp; Short-term<br>Investment Decisions</div>
  </div>
  <div class="service service--gold service--performance">
    <div class="service__inner">Performance<br>Evaluation</div>
  </div>
  <div class="service service--navy service--budgeting">
    <div class="service__inner">Budgeting &amp;<br>Strategic Planning</div>
  </div>
  <div class="service service--gold service--risk">
    <div class="service__inner">Risk<br>Management</div>
  </div>
  <div class="service service--navy service--compliance">
    <div class="service__inner">Compliance:<br>Tax, Legal and<br>Regulator</div>
  </div>
  <div class="service service--gold service--communication">
    <div class="service__inner">Comunication:
      <span class="service__detail">Board of Directors,<br>Creditors, Owners,<br>Investors, Credit<br>Rating Agencies</span>
    </div>
  </div>
</main>
</body>
</html>
```